Vorn upkeep KT Solar Venture

Solar power system install
Services and maintenance
wiring, Rewinding and Renovation
Switch Board Upgrade
Power and lighting point
t doesn’t matter how much you spend on quality parts, your solar system will let you down if your design and installation are sub-par. Have your solar system tailored and installed by our Master Electrician and Bright Grid Guild Accredited team.

Target Market(s)

sales and installed

Industry/Entity Type

Solar install and retailer

Contact Information for Business Card

Name , Email, Phone Number ,Business address,

Font styles to use
Serif

Colors
0054AA
0677BA
7BADD7
CADEEF
E8F1F8

Requirements
Must have
• clear and bright
Nice to have
• new design
Should not have
• unclear pictures

```html
<!DOCTYPE html>
<html lang="en">
<head>
<meta charset="utf-8">
<title>Vorn upkeep KT Solar Venture – Business Card</title>
<link rel="stylesheet" href="https://fonts.googleapis.com/css2?family=Roboto:wght@400;500;700&family=Saira+Condensed:wght@700&display=swap">
<style>
  :root {
    --stage: #2a2a2a;
    --card: #f1f1f1;
    --brand-blue: #0054AA;
    --mid-blue: #0677BA;
    --sky: #7BADD7;
    --pale: #CADEEF;
    --mist: #E8F1F8;
    --leaf: #1e9a3c;
    --band-green: #5fa23a;
    --band-blue: #0b72b4;
    --ink: #1d1d1d;
    --sun: #f2b705;
  }
  * { margin: 0; padding: 0; box-sizing: border-box; }
  html, body { width: 1200px; height: 1138px; overflow: hidden; }
  body {
    background: var(--stage);
    font-family: "Roboto", Arial, sans-serif;
    position: relative;
  }
  .card {
    position: absolute;
    width: 620px;
    height: 375px;
    background: var(--card);
    border-radius: 14px;
    overflow: hidden;
  }
  .card--front { left: 274px; top: 186px; }
  .card--back { left: 277px; top: 608px; }

  .wordmark {
    font-family: "Saira Condensed", "Arial Narrow", sans-serif;
    font-weight: 700;
    color: var(--brand-blue);
    text-transform: uppercase;
    line-height: 1;
  }
  .front-brand {
    position: absolute;
    left: 104px;
    top: 88px;
    display: flex;
    align-items: center;
    gap: 22px;
  }
  .brand-dot {
    width: 104px;
    height: 104px;
    border-radius: 50%;
    background: linear-gradient(160deg, var(--sun), var(--mid-blue) 70%, var(--leaf));
  }
  .front-brand .wordmark { font-size: 41px; letter-spacing: 0.5px; }
  .front-brand .wordmark span { display: block; }
  .front-brand .wordmark span + span { letter-spacing: 3px; margin-top: 2px; }

  .service-band {
    position: absolute;
    left: 0; top: 239px;
    width: 100%; height: 74px;
    background: linear-gradient(90deg, var(--band-green) 0%, #3b9178 45%, var(--band-blue) 75%);
    color: var(--mist);
    font-size: 16.5px;
    text-align: center;
    display: flex;
    flex-direction: column;
    justify-content: center;
    gap: 5px;
  }
  .site-line {
    position: absolute;
    left: 0; top: 333px;
    width: 100%;
    display: flex;
    justify-content: center;
    align-items: center;
    gap: 28px;
    font-size: 16px;
    color: var(--ink);
  }
  .site-line .rule { width: 80px; height: 2px; }
  .rule--blue { background: linear-gradient(90deg, transparent, var(--mid-blue)); }
  .rule--green { background: linear-gradient(90deg, var(--leaf), transparent); }

  .back-brand { position: absolute; left: 32px; top: 32px; font-size: 31px; }
  .back-brand span { display: block; }
  .back-brand span + span { letter-spacing: 2.5px; margin-top: 2px; }

  .person { position: absolute; left: 32px; top: 146px; }
  .person-name { font-size: 25px; font-weight: 700; color: var(--brand-blue); }
  .person-role { font-size: 15.5px; color: var(--ink); margin-top: 3px; }

  .address { position: absolute; left: 32px; top: 222px; font-size: 15.5px; color: var(--ink); line-height: 23px; }

  .contacts { position: absolute; left: 32px; top: 274px; list-style: none; font-size: 15.5px; color: var(--ink); }
  .contacts li { display: flex; align-items: center; height: 23.5px; }
  .contacts svg { width: 15px; height: 15px; margin-right: 17px; fill: var(--leaf); }

  .emblem {
    position: absolute;
    left: 316px; top: 104px;
    width: 240px; height: 240px;
    border-radius: 50%;
    background: radial-gradient(circle at 45% 35%, var(--sun) 0%, var(--sky) 45%, var(--mid-blue) 75%, var(--leaf) 100%);
  }
</style>
</head>
<body>
  <section class="card card--front" aria-label="Business card front">
    <div class="front-brand">
      <div class="brand-dot"></div>
      <div class="wordmark"><span>Vorn upkeep</span><span>KT Solar Venture</span></div>
    </div>
    <div class="service-band">
      <p>Solar Power System Install &nbsp;|&nbsp; Wiring, Rewinding &amp; Renovation</p>
      <p>Services &amp; Maintenance &nbsp;|&nbsp; Switch Board Upgrade &nbsp;|&nbsp; Power &amp; Lighting Point</p>
    </div>
    <div class="site-line">
      <span class="rule rule--blue"></span>
      <span>www.ktsolarventure.com</span>
      <span class="rule rule--green"></span>
    </div>
  </section>

  <section class="card card--back" aria-label="Business card back">
    <div class="wordmark back-brand"><span>Vorn upkeep</span><span>KT Solar Venture</span></div>
    <div class="person">
      <p class="person-name">Ravi Lente Moor</p>
      <p class="person-role">Managing Director</p>
    </div>
    <p class="address">18 Harrow Lane, Kestle Bay,<br>Westmere, US 402718</p>
    <ul class="contacts">
      <li><svg viewBox="0 0 16 16" aria-hidden="true"><path d="M1 6c0-2 3-4 7-4s7 2 7 4l-3 1-1-2H5L4 7 1 6zm3 2h8l2 6H2l2-6zm4 1.5a2 2 0 1 0 0 4 2 2 0 0 0 0-4z"/></svg>555-204-7731</li>
      <li><svg viewBox="0 0 16 16" aria-hidden="true"><path d="M1 3h14v10H1V3zm1.5 1.5L8 9l5.5-4.5v-.2H2.5v.2z"/></svg>ravi@ktsolarventure.com</li>
      <li><svg viewBox="0 0 16 16" aria-hidden="true"><path d="M8 1a7 7 0 1 0 0 14A7 7 0 0 0 8 1zm0 1.5c.8 0 1.7 1.6 2 4H6c.3-2.4 1.2-4 2-4zM6 8h4c0 .5 0 1-.1 1.5H6.1C6 9 6 8.5 6 8zm-3.5 0h2c0 .5 0 1 .1 1.5H2.7A5.5 5.5 0 0 1 2.5 8zm9 0h2c0 .5-.1 1-.2 1.5h-1.9c.1-.5.1-1 .1-1.5zM8 13.5c-.8 0-1.6-1.3-1.9-2.5h3.8c-.3 1.2-1.1 2.5-1.9 2.5z"/></svg>www.ktsolarventure.com</li>
    </ul>
    <div class="emblem"></div>
  </section>
</body>
</html>
```